Veltrano.co - Arctic Voyage Specialists

We need a modern, visually striking business card for Veltrano.co, a company specialized in selling expedition cruises to the most remote regions on Earth, with a focus on the Arctic and Antarctica. The design should instantly communicate that the cardholder is an expert in polar travel. Use clean, premium aesthetics with cool tones like icy blue and white, possibly incorporating polar imagery (ice, glaciers, penguins, etc.)

Attached the logo

Contact Information for Business Card

Feels high-end and trustworthy.. Visually memorable — encourages people to keep it

Colors
0054AA
0677BA
7BADD7
CADEEF
E8F1F8

Requirements
Must have
• ice, glaciers, penguins, montains
Nice to have
• modern, transparente,

```html
<!DOCTYPE html>
<html lang="en">
<head>
<meta charset="utf-8">
<title>Veltrano.co Business Card</title>
<link rel="stylesheet" href="https://fonts.googleapis.com/css2?family=Poppins:wght@600;700&family=Montserrat:wght@400;700&display=swap">
<style>
  :root {
    --brand-blue: #2e75b9;
    --ink: #3a3f47;
    --card-white: #ffffff;
    --backdrop: #eceef1;
    --photo-top: #6199cc;
    --photo-mid: #5a92c8;
    --photo-bottom: #4a85bf;
    --white: #ffffff;
  }
  html, body {
    margin: 0;
    padding: 0;
    width: 1192px;
    height: 1200px;
    overflow: hidden;
    background: var(--backdrop);
  }
  .canvas {
    position: relative;
    width: 1192px;
    height: 1200px;
  }
  .card {
    position: absolute;
    left: 219px;
    width: 754px;
    height: 432px;
    border-radius: 38px;
    overflow: hidden;
    box-shadow: 0 12px 26px rgba(0, 0, 0, 0.16);
  }
  .card-front { top: 145px; background: var(--card-white); }
  .card-back  { top: 622px; }

  .brand-mark {
    position: absolute;
    border-radius: 50%;
    background: var(--brand-blue);
  }
  .front-mark { left: 46px; top: 72px; width: 54px; height: 54px; }

  .brand-name {
    position: absolute;
    margin: 0;
    font-family: "Poppins", sans-serif;
    font-weight: 700;
    line-height: 1;
    color: var(--brand-blue);
    white-space: nowrap;
  }
  .front-name { left: 139px; top: 80px; font-size: 48px; }

  .brand-tagline {
    position: absolute;
    margin: 0;
    font-family: "Poppins", sans-serif;
    font-weight: 600;
    line-height: 1;
    color: var(--brand-blue);
    white-space: nowrap;
  }
  .front-tagline { left: 139px; top: 131px; font-size: 14px; }

  .name-bar {
    position: absolute;
    left: 0;
    top: 286px;
    width: 18px;
    height: 48px;
    background: var(--brand-blue);
  }
  .holder-name {
    position: absolute;
    left: 36px;
    top: 281px;
    margin: 0;
    font-family: "Montserrat", sans-serif;
    font-weight: 700;
    font-size: 30px;
    line-height: 1;
    color: var(--brand-blue);
    letter-spacing: 0.5px;
  }
  .holder-role {
    position: absolute;
    left: 36px;
    top: 314px;
    margin: 0;
    font-family: "Montserrat", sans-serif;
    font-weight: 400;
    font-size: 20px;
    line-height: 1;
    color: var(--ink);
  }

  .contact {
    position: absolute;
    left: 395px;
    top: 236px;
    font-family: "Montserrat", sans-serif;
    font-weight: 400;
    font-size: 18px;
    color: var(--ink);
  }
  .address { margin: 0 0 16px 0; line-height: 23px; }
  .contact-list { list-style: none; margin: 0; padding: 0; }
  .contact-list li {
    display: flex;
    align-items: center;
    height: 30.5px;
  }
  .contact-icon {
    width: 13px;
    height: 13px;
    margin-right: 8px;
    fill: var(--brand-blue);
    flex: none;
  }

  .back-photo {
    position: absolute;
    inset: 0;
    background:
      radial-gradient(ellipse 45% 60% at 55% 55%, rgba(255,255,255,0.14), rgba(255,255,255,0) 70%),
      linear-gradient(180deg, var(--photo-top) 0%, var(--photo-mid) 55%, var(--photo-bottom) 100%);
  }
  .back-mark { left: 148px; top: 162px; width: 88px; height: 88px; background: var(--white); }
  .back-name { left: 281px; top: 180px; font-size: 70px; color: var(--white); }
  .back-tagline { left: 281px; top: 252px; font-size: 20px; color: var(--white); }
</style>
</head>
<body>
<main class="canvas">
  <section class="card card-front" aria-label="Business card front">
    <span class="brand-mark front-mark" aria-hidden="true"></span>
    <h1 class="brand-name front-name">Veltrano.co</h1>
    <p class="brand-tagline front-tagline">Arctic Voyage Specialists</p>

    <span class="name-bar" aria-hidden="true"></span>
    <h2 class="holder-name">MARCO LIND</h2>
    <p class="holder-role">CEO / Founder</p>

    <div class="contact">
      <p class="address">P.O. Box 3126 Harbor Lane<br>Nordvik County NR 4817</p>
      <ul class="contact-list">
        <li>
          <svg class="contact-icon" viewBox="0 0 16 16" aria-hidden="true"><path d="M1 6c0-2 3-4 7-4s7 2 7 4v1.5h-3.5V6H4.5v1.5H1z"/><path d="M3 9l2-2h6l2 2v5H3z"/></svg>
          <span>+41 555 20 73 918</span>
        </li>
        <li>
          <svg class="contact-icon" viewBox="0 0 16 16" aria-hidden="true"><path d="M1 6l7-5 7 5v9H1z"/><path d="M2.5 7l5.5 4 5.5-4" fill="none" stroke="#fff" stroke-width="1.3"/></svg>
          <span>marco.lind@veltrano.co</span>
        </li>
        <li>
          <svg class="contact-icon" viewBox="0 0 16 16" aria-hidden="true"><circle cx="8" cy="8" r="7"/><path d="M5 4c1 1 2 1 2 3s-2 1-2 3M10 3c-1 2 1 3 2 3M10 13c0-2 2-2 3-3" fill="none" stroke="#fff" stroke-width="1.2"/></svg>
          <span>www.veltrano.co</span>
        </li>
      </ul>
    </div>
  </section>

  <section class="card card-back" aria-label="Business card back">
    <div class="back-photo" role="img" aria-label="Blue-tinted photograph of a polar bear walking on snow and ice"></div>
    <span class="brand-mark back-mark" aria-hidden="true"></span>
    <p class="brand-name back-name">Veltrano.co</p>
    <p class="brand-tagline back-tagline">Arctic Voyage Specialists</p>
  </section>
</main>
</body>
</html>
```